Board Presentation template

Design a simple and clean PowerPoint slide templates for a Board meeting. The slides should have predominantly white backgrounds and use the colors of our Logo (attached): Tones of grey and orange and blue.
The company name is called Keystone Lane Gauging.
It sell, calibrate, service and repair industrial and commercial scales of all types. In particular, Truck scales, floor scales, counting scales and benchtop scales.
There is no website for Keystone Lane Gauging, but we have three affiliates that have their own websites:
https://www.fernwaybalance.example/
https://meadowlarkhandlingandmassing.example/
https://tvbalance.example/
Target Market(s)
Industrial and Commercial Weighing systems
Industry/Entity Type
Look and feel

```html
<!DOCTYPE html>
<html lang="en">
<head>
<meta charset="utf-8">
<title>Keystone Lane Gauging — Board Presentation</title>
<link rel="stylesheet" href="https://fonts.googleapis.com/css2?family=Oswald:wght@500;600;700&family=Roboto:wght@400;500;700&display=swap">
<style>
:root{
  --board:#dedfe0;
  --white:#ffffff;
  --blue:#2b5f8b;
  --slate:#414d58;
  --slate-photo:#56697a;
  --red:#d3322c;
  --ink:#2e2e2e;
  --muted:#555c63;
  --faint:#ececec;
}
*{box-sizing:border-box;margin:0;padding:0}
html,body{width:1026px;height:1200px;overflow:hidden;background:var(--board)}
body{position:relative;font-family:'Roboto',Arial,sans-serif;color:var(--ink)}
.slide{position:absolute;width:469px;height:263px;background:var(--white);overflow:hidden;box-shadow:0 1px 3px rgba(0,0,0,.12)}
.col-left{left:30px}.col-right{left:527px}
.row-1{top:33px}.row-2{top:323px}.row-3{top:613px}.row-4{top:903px}
.top-band{position:absolute;left:0;top:0;width:100%;height:7px;background:var(--slate);border-bottom:2px solid var(--blue)}
.slide-title{position:absolute;left:0;width:100%;text-align:center;font-family:'Oswald',sans-serif;font-weight:600;font-size:14px;letter-spacing:.3px;color:var(--slate)}
.slide-title .accent{color:var(--blue)}
.title-rule{position:absolute;left:50%;width:33px;height:1.5px;margin-left:-16.5px;background:var(--blue)}
.brand{position:absolute;text-align:center;font-family:'Oswald',sans-serif;font-weight:500;color:var(--slate);line-height:1.05}
.brand .dot{display:block;margin:0 auto 2px;border:1.5px solid var(--slate);border-radius:50%}
.footer-brand{left:9px;top:227px;width:46px;font-size:5.6px}
.footer-brand .dot{width:10px;height:10px}
.footer-line{position:absolute;left:64px;top:250px;width:356px;height:2px;background:var(--blue)}
.page-tab{position:absolute;right:0;top:243px;width:56px;height:20px;background:var(--blue);clip-path:polygon(8% 0,100% 0,100% 100%,0 100%);color:var(--white);font-size:5px;line-height:20px;text-align:center;padding-left:4px}
.photo{position:absolute}
/* cover */
.cover-photo{inset:0;background:linear-gradient(180deg,#c9d3dc 0%,#dfe5ea 45%,#7d8389 62%,#55595d 100%)}
.cover-brand{left:22px;top:14px;width:74px;font-size:9px}
.cover-brand .dot{width:18px;height:18px;border-color:var(--slate)}
.cover-card{position:absolute;left:251px;top:215px;width:218px;height:48px;background:var(--white);padding:9px 0 0 18px}
.cover-bar{position:absolute;left:329px;top:207px;width:140px;height:8px;background:var(--blue)}
.cover-kicker{font-size:9px;color:var(--red);letter-spacing:.2px}
.cover-title{font-family:'Oswald',sans-serif;font-weight:600;font-size:17px;color:var(--slate);line-height:1.25}
.partner{position:absolute;top:228px;height:22px;background:rgba(255,255,255,.85)}
/* solution */
.product{position:absolute;top:63px;width:91px}
.product .photo{position:relative;width:91px;height:79px}
.product h3{margin-top:7px;text-align:center;font-size:7px;font-weight:500;color:var(--ink)}
.product .rule{width:12px;height:1px;background:var(--blue);margin:4px auto 6px}
.product p{text-align:center;font-size:4.4px;line-height:7.3px;color:var(--muted)}
/* agenda */
.agenda-panel{left:0;top:0;width:200px;height:263px;background:linear-gradient(180deg,#4e5f6e 0%,#5f7181 55%,#495a69 100%)}
.agenda-title{position:absolute;left:71px;top:98px;font-family:'Oswald',sans-serif;font-weight:600;font-size:17px;color:var(--white)}
.agenda-rule{position:absolute;left:70px;top:131px;width:33px;height:1px;background:var(--white)}
.agenda-brand{left:424px;top:5px;width:42px;font-size:5.4px}
.agenda-brand .dot{width:11px;height:11px}
.agenda-item{position:absolute;left:182px;height:36px;width:270px}
.icon-ring{position:absolute;left:0;top:0;width:36px;height:36px;border-radius:50%;background:var(--blue);border:2.5px solid var(--white);box-shadow:0 0 0 1px #c9d2da}
.icon-ring svg{position:absolute;left:8px;top:8px}
.agenda-item h4{position:absolute;left:44px;top:4px;font-size:6px;font-weight:700;color:var(--ink)}
.agenda-item p{position:absolute;left:44px;top:14px;width:180px;font-size:4.3px;line-height:6px;color:var(--muted)}
.page-plain{position:absolute;left:424px;top:248px;font-size:5px;color:var(--ink)}
/* data */
.chart{position:absolute;left:28px;top:54px}
.data-item{position:absolute;left:260px;width:200px;height:30px}
.data-item .icon-ring{width:28px;height:28px;background:var(--blue);border:2px solid var(--white);box-shadow:0 0 0 1.5px var(--slate)}
.data-item .icon-ring svg{left:5px;top:5px}
.data-item h4{position:absolute;left:35px;top:2px;font-size:5.6px;font-weight:700}
.data-item p{position:absolute;left:35px;top:11px;width:115px;font-size:4.3px;line-height:7px;color:var(--muted)}
/* about */
.about-copy{position:absolute;left:32px;top:60px;width:186px;font-size:5.6px;line-height:9.8px;color:var(--muted);text-align:justify}
.about-copy p+p{margin-top:9.8px}
.about-frame{position:absolute;left:245px;top:134px;width:95px;height:85px;background:var(--blue)}
.about-photo{left:252px;top:58px;width:187px;height:154px;background:linear-gradient(180deg,#d8e0e4 0%,#b9c2b0 38%,#e7e9ea 55%,#a8a49c 100%)}
/* divider */
.divider-mark{position:absolute;left:201px;top:80px;width:67px;height:67px;border-radius:50%;border:5px solid var(--faint)}
.divider-name{position:absolute;left:0;width:100%;top:160px;text-align:center;font-family:'Oswald',sans-serif;font-weight:600;font-size:16px;color:var(--faint);letter-spacing:.5px}
/* why */
.why-copy{position:absolute;left:40px;top:57px;width:389px;text-align:center;font-size:5.8px;line-height:8.6px;color:var(--muted)}
.reason{position:absolute;top:100px;width:98px;height:120px}
.reason .ring{position:absolute;left:28px;top:0;width:42px;height:42px;border-radius:50%;border:2.5px solid var(--slate);background:var(--white)}
.reason .ring svg{position:absolute;left:6px;top:6px}
.reason .stem{position:absolute;left:48px;top:42px;width:2px;height:14px;background:var(--slate)}
.reason h4{position:absolute;left:0;top:56px;width:98px;height:20px;background:var(--slate);color:var(--white);font-size:6px;font-weight:500;text-align:center;line-height:20px}
.reason p{position:absolute;left:4.5px;top:78px;width:89px;height:42px;background:var(--blue);color:var(--white);font-size:4.6px;line-height:7.3px;text-align:center;padding-top:6px}
/* thank you */
.thanks-photo{inset:0;background:linear-gradient(135deg,#5a6c7c 0%,#6a7d8e 50%,#4f6070 100%)}
.thanks-rule{position:absolute;left:218px;top:98px;width:33px;height:1px;background:var(--white)}
.thanks-title{position:absolute;left:0;width:100%;top:104px;text-align:center;font-family:'Oswald',sans-serif;font-weight:700;font-size:46px;color:var(--white);letter-spacing:1px;line-height:1}
</style>
</head>
<body>

<!-- Cover -->
<section class="slide col-left row-1">
  <div class="photo cover-photo" role="img" aria-label="White semi trucks driving in convoy along an open highway"></div>
  <div class="brand cover-brand"><span class="dot"></span>KEYSTONE LANE<br>GAUGING</div>
  <div class="partner" style="left:82px;width:30px;border-radius:50%"></div>
  <div class="partner" style="left:122px;width:76px;border-radius:3px"></div>
  <div class="partner" style="left:206px;width:30px"></div>
  <div class="cover-bar"></div>
  <div class="cover-card">
    <div class="cover-kicker">INTRODUCTION</div>
    <div class="cover-title">KEYSTONE LANE GAUGING</div>
  </div>
</section>

<!-- Our solution -->
<section class="slide col-right row-1">
  <div class="top-band"></div>
  <h2 class="slide-title" style="top:18px">OUR SOLUTION</h2>
  <div class="title-rule" style="top:45px"></div>
  <div class="product" style="left:39px">
    <div class="photo" role="img" aria-label="Truck on a weighbridge under a steel canopy" style="background:linear-gradient(180deg,#8e9aa4,#c7cdd2 60%,#6f7378)"></div>
    <h3>Truck scales</h3><div class="rule"></div>
    <p>Lorem ipsum dolor sit amet, consectetur adipiscing elit, sed do eiusmod tempor incididunt ut labore et dolore magna aliqua. Ut enim ad minim veniam quis nostrud exercit</p>
  </div>
  <div class="product" style="left:137.5px">
    <div class="photo" role="img" aria-label="Dial floor scale on a wooden floor" style="background:linear-gradient(180deg,#3a3a3a,#6d6a66 40%,#c79a62 70%,#d9b07a)"></div>
    <h3>Floor scales</h3><div class="rule"></div>
    <p>Lorem ipsum dolor sit amet, consectetur adipiscing elit, sed do eiusmod tempor incididunt ut labore et dolore magna aliqua. Ut enim ad minim veniam quis nostrud exercit</p>
  </div>
  <div class="product" style="left:236px">
    <div class="photo" role="img" aria-label="Counting scale keypad with yellow display" style="background:linear-gradient(135deg,#8a8d92,#c9cfd6 50%,#5b5e62)"></div>
    <h3>Counting scales</h3><div class="rule"></div>
    <p>Lorem ipsum dolor sit amet, consectetur adipiscing elit, sed do eiusmod tempor incididunt ut labore et dolore magna aliqua. Ut enim ad minim veniam quis nostrud exercit</p>
  </div>
  <div class="product" style="left:334.5px">
    <div class="photo" role="img" aria-label="White digital benchtop scale on a grey counter" style="background:linear-gradient(135deg,#7d8084,#c2c5c8 45%,#eef0f1 70%,#a9acaf)"></div>
    <h3>Benchtop scales</h3><div class="rule"></div>
    <p>Lorem ipsum dolor sit amet, consectetur adipiscing elit, sed do eiusmod tempor incididunt ut labore et dolore magna aliqua. Ut enim ad minim veniam quis nostrud exercit</p>
  </div>
  <div class="brand footer-brand"><span class="dot"></span>KEYSTONE LANE<br>GAUGING</div>
  <div class="footer-line"></div>
  <div class="page-tab">Page No : 05</div>
</section>

<!-- Agenda -->
<section class="slide col-left row-2">
  <div class="photo agenda-panel" role="img" aria-label="Dark truck on a road under a cloudy sky, blue-grey tint"></div>
  <h2 class="agenda-title">AGENDA</h2>
  <div class="agenda-rule"></div>
  <div class="brand agenda-brand"><span class="dot"></span>KEYSTONE LANE<br>GAUGING</div>

  <div class="agenda-item" style="top:44.5px">
    <div class="icon-ring"><svg width="20" height="20" viewBox="0 0 20 20" fill="none" stroke="#fff" stroke-width="1.2"><circle cx="7" cy="12" r="4"/><circle cx="7" cy="12" r="1.3"/><circle cx="14" cy="6" r="3"/><circle cx="14" cy="6" r="1"/></svg></div>
    <h4>Lorem ipsum dolor sit</h4>
    <p>Lorem ipsum dolor sit amet, consectetur adipiscing elit, sed do eiusmod tempor incididunt ut labore et dolore magna aliqua.</p>
  </div>
  <div class="agenda-item" style="top:95.5px">
    <div class="icon-ring"><svg width="20" height="20" viewBox="0 0 20 20" fill="none" stroke="#fff" stroke-width="1.2"><rect x="4" y="3" width="12" height="12" rx="1"/><line x1="4" y1="9" x2="16" y2="9"/><line x1="2" y1="17" x2="18" y2="17"/></svg></div>
    <h4>Lorem ipsum dolor sit</h4>
    <p>Lorem ipsum dolor sit amet, consectetur adipiscing elit, sed do eiusmod tempor incididunt ut labore et dolore magna aliqua.</p>
  </div>
  <div class="agenda-item" style="top:146.5px">
    <div class="icon-ring"><svg width="20" height="20" viewBox="0 0 20 20" fill="none" stroke="#fff" stroke-width="1.2"><circle cx="10" cy="9" r="6"/><circle cx="10" cy="9" r="2.2"/><line x1="10" y1="15" x2="10" y2="19"/></svg></div>
    <h4>Lorem ipsum dolor sit</h4>
    <p>Lorem ipsum dolor sit amet, consectetur adipiscing elit, sed do eiusmod tempor incididunt ut labore et dolore magna aliqua.</p>
  </div>
  <div class="agenda-item" style="top:197.5px">
    <div class="icon-ring"><svg width="20" height="20" viewBox="0 0 20 20" fill="none" stroke="#fff" stroke-width="1.2"><rect x="3" y="8" width="5" height="10"/><rect x="9" y="4" width="5" height="14"/><line x1="15" y1="18" x2="18" y2="18"/><polyline points="14,4 17,2 17,18"/></svg></div>
    <h4>Lorem ipsum dolor sit</h4>
    <p>Lorem ipsum dolor sit amet, consectetur adipiscing elit, sed do eiusmod tempor incididunt ut labore et dolore magna aliqua.</p>
  </div>
  <div class="page-plain">Page No : 02</div>
</section>

<!-- Our data -->
<section class="slide col-right row-2">
  <div class="top-band"></div>
  <h2 class="slide-title" style="top:18px">OUR <span class="accent">DATA</span></h2>
  <div class="title-rule" style="top:46px"></div>
  <svg class="chart" width="220" height="170" viewBox="0 0 220 170" font-family="Roboto, Arial, sans-serif" font-size="4.6" fill="#444">
    <g text-anchor="end">
      <text x="10" y="155">0</text><text x="10" y="140.4">1</text><text x="10" y="125.8">2</text><text x="10" y="111.2">3</text><text x="10" y="96.6">4</text><text x="10" y="82">5</text><text x="10" y="67.4">6</text><text x="10" y="52.8">7</text><text x="10" y="38.2">8</text><text x="10" y="23.6">9</text><text x="10" y="9">10</text>
    </g>
    <line x1="28" y1="152" x2="28" y2="6" stroke="#c9c9c9" stroke-width=".6"/>
    <line x1="28" y1="152" x2="205" y2="152" stroke="#c9c9c9" stroke-width=".6"/>
    <rect x="40" y="86.3" width="11" height="65.7" fill="var(--slate)"/>
    <rect x="68" y="79" width="11" height="73" fill="var(--blue)"/>
    <rect x="96" y="48.3" width="11" height="103.7" fill="var(--slate)"/>
    <rect x="124.5" y="79" width="11" height="73" fill="var(--blue)"/>
    <rect x="152.5" y="86.3" width="11" height="65.7" fill="var(--slate)"/>
    <rect x="180.5" y="48.3" width="11" height="103.7" fill="var(--blue)"/>
    <g text-anchor="middle" fill="#666">
      <text x="45.5" y="82">4.5%</text><text x="73.5" y="74.5">5%</text><text x="101.5" y="44">7.1%</text><text x="130" y="74.5">5%</text><text x="158" y="82">4.5%</text><text x="186" y="44">7.1%</text>
    </g>
    <g text-anchor="middle">
      <text x="45.5" y="160">2000</text><text x="73.5" y="160">2005</text><text x="101.5" y="160">2010</text><text x="130" y="160">2015</text><text x="158" y="160">2020</text><text x="186" y="160">2024</text>
    </g>
  </svg>
  <div class="data-item" style="top:56.5px">
    <div class="icon-ring"><svg width="18" height="18" viewBox="0 0 18 18" fill="none" stroke="#fff" stroke-width="1.1"><rect x="3" y="5" width="12" height="7"/><line x1="2" y1="15" x2="16" y2="15"/></svg></div>
    <h4>Lorem ipsum dolor sit amet</h4>
    <p>Lorem ipsum dolor sit amet, consectetur adipiscing elit, sed do eiusmod tempor incididunt ut</p>
  </div>
  <div class="data-item" style="top:99px">
    <div class="icon-ring"><svg width="18" height="18" viewBox="0 0 18 18" fill="none" stroke="#fff" stroke-width="1.1"><circle cx="7" cy="11" r="4"/><circle cx="13" cy="5" r="2.5"/></svg></div>
    <h4>Lorem ipsum dolor sit amet</h4>
    <p>Lorem ipsum dolor sit amet, consectetur adipiscing elit, sed do eiusmod tempor incididunt ut</p>
  </div>
  <div class="data-item" style="top:141px">
    <div class="icon-ring"><svg width="18" height="18" viewBox="0 0 18 18" fill="none" stroke="#fff" stroke-width="1.1"><circle cx="8" cy="10" r="5"/><circle cx="8" cy="10" r="1.6"/><line x1="12" y1="3" x2="16" y2="3"/></svg></div>
    <h4>Lorem ipsum dolor sit amet</h4>
    <p>Lorem ipsum dolor sit amet, consectetur adipiscing elit, sed do eiusmod tempor incididunt ut</p>
  </div>
  <div class="data-item" style="top:183.5px">
    <div class="icon-ring"><svg width="18" height="18" viewBox="0 0 18 18" fill="none" stroke="#fff" stroke-width="1.1"><circle cx="9" cy="9" r="6"/><circle cx="9" cy="9" r="3"/><circle cx="9" cy="9" r="1"/></svg></div>
    <h4>Lorem ipsum dolor sit amet</h4>
    <p>Lorem ipsum dolor sit amet, consectetur adipiscing elit, sed do eiusmod tempor incididunt ut</p>
  </div>
  <div class="brand footer-brand"><span class="dot"></span>KEYSTONE LANE<br>GAUGING</div>
  <div class="footer-line"></div>
  <div class="page-tab">Page No : 06</div>
</section>

<!-- About us -->
<section class="slide col-left row-3">
  <div class="top-band"></div>
  <h2 class="slide-title" style="top:13px">ABOUT US</h2>
  <div class="title-rule" style="top:40px"></div>
  <div class="about-copy">
    <p>Lorem ipsum dolor sit amet, consectetur adipiscing elit, sed do eiusmod tempor incididunt ut labore et dolore magna aliqua. Ut enim ad minim veniam, quis nostrud exercitation ullamco laboris nisi ut aliquip ex ea commodo consequat.</p>
    <p>Duis aute irure dolor in reprehenderit in voluptate velit esse cillum dolore eu fugiat nulla pariatur. Excepteur sint occaecat cupidatat non proident, sunt in culpa qui officia deserunt mollit anim id est laborum. Lorem ipsum dolor sit amet, consectetur adipiscing elit, sed do eiusmod tempor incididunt ut labore et dolore magna aliqua. Ut enim ad minim veniam, quis nostrud exercitation ullamco laboris nisi ut aliquip ex ea commodo consequat. Duis aute irure dolor in reprehenderit in voluptate velit esse cillum dolore eu fugiat nulla pariatur.</p>
  </div>
  <div class="about-frame"></div>
  <div class="photo about-photo" role="img" aria-label="Concrete weighbridge beside white site offices under trees"></div>
  <div class="brand footer-brand"><span class="dot"></span>KEYSTONE LANE<br>GAUGING</div>
  <div class="footer-line"></div>
  <div class="page-tab">Page No : 03</div>
</section>

<!-- Section divider -->
<section class="slide col-right row-3">
  <div class="top-band"></div>
  <h2 class="slide-title" style="top:13px">SECTION <span class="accent">DIVIDER</span></h2>
  <div class="title-rule" style="top:40px"></div>
  <div class="divider-mark"></div>
  <div class="divider-name">KEYSTONE LANE GAUGING</div>
  <div class="brand footer-brand"><span class="dot"></span>KEYSTONE LANE<br>GAUGING</div>
  <div class="footer-line"></div>
  <div class="page-tab">Page No : 07</div>
</section>

<!-- Why choose us -->
<section class="slide col-left row-4">
  <div class="top-band"></div>
  <h2 class="slide-title" style="top:20px">WHY <span class="accent">CHOOSE US</span></h2>
  <div class="title-rule" style="top:47px"></div>
  <p class="why-copy">Lorem ipsum dolor sit amet, consectetur adipiscing elit, sed do eiusmod tempor incididunt ut labore et dolore magna aliqua. Ut enim ad minim veniam, quis nostrud exercitation ullamco laboris nisi ut aliquip ex ea commodo consequat. Duis aute irure dolor in reprehenderit in voluptate velit esse cillum dolore eu fugiat nulla pariatur. Excepteur sint occaecat cupidatat non proident, sunt in culpa qui officia deserunt mollit anim id est laborum.</p>

  <div class="reason" style="left:58px">
    <div class="ring"><svg width="26" height="26" viewBox="0 0 26 26" fill="none" stroke="var(--red)" stroke-width="1.6"><circle cx="13" cy="13" r="9"/><text x="13" y="16" text-anchor="middle" font-family="Roboto, Arial, sans-serif" font-size="8" font-weight="700" fill="var(--red)" stroke="none">24</text></svg></div>
    <div class="stem"></div>
    <h4>24/7 Emergency Services</h4>
    <p>Lorem ipsum dolor sit amet, consectetur adipiscing elit, sed do eiusmod tempor incididunt ut labore et dolore magna aliqua.</p>
  </div>
  <div class="reason" style="left:185.5px">
    <div class="ring"><svg width="26" height="26" viewBox="0 0 26 26" fill="none" stroke="var(--red)" stroke-width="1.6"><path d="M7 4h9l4 4v14H7z" fill="var(--red)" stroke="none"/><line x1="10" y1="11" x2="17" y2="11" stroke="#fff"/><line x1="10" y1="14" x2="15" y2="14" stroke="#fff"/><polyline points="14,19 16,21 20,17" stroke="#fff"/></svg></div>
    <div class="stem"></div>
    <h4>Accredited</h4>
    <p>Lorem ipsum dolor sit amet, consectetur adipiscing elit, sed do eiusmod tempor incididunt ut labore et dolore magna aliqua.</p>
  </div>
  <div class="reason" style="left:313px">
    <div class="ring"><svg width="26" height="26" viewBox="0 0 26 26" fill="none" stroke="var(--red)" stroke-width="1.6"><circle cx="13" cy="11" r="7"/><circle cx="13" cy="11" r="2.5"/><line x1="10" y1="18" x2="10" y2="22"/><line x1="16" y1="18" x2="16" y2="22"/></svg></div>
    <div class="stem"></div>
    <h4>Comprehensive</h4>
    <p>Lorem ipsum dolor sit amet, consectetur adipiscing elit, sed do eiusmod tempor incididunt ut labore et dolore magna aliqua.</p>
  </div>
  <div class="brand footer-brand"><span class="dot"></span>KEYSTONE LANE<br>GAUGING</div>
  <div class="footer-line"></div>
  <div class="page-tab">Page No : 04</div>
</section>

<!-- Thank you -->
<section class="slide col-right row-4">
  <div class="photo thanks-photo" role="img" aria-label="Hands writing at a desk beside a laptop, blue-grey tint"></div>
  <div class="thanks-rule"></div>
  <h2 class="thanks-title">THANK YOU</h2>
</section>

</body>
</html>
```